Redesign current business card for food company

i would like to redesign my business card. our company is food company, our product range from chips, juices, milk and etc (mostly dried food stuff).
I want o keep same logo but , the rest is open to new design.
you can check at our website about our company www.orvelpantry.com

Target Market(s)

most of food company

Industry/Entity Type

Business

Contact Information for Business Card

I want to keep more to blue color...

Colors
3176b5
abd036

Requirements
Must have
• our old logo
Nice to have
• we do not mind to have nice material on bus card in order to accomplish nice design. for example: using spot uv, embossed and etc.

```html
<!DOCTYPE html>
<html lang="en">
<head>
<meta charset="utf-8">
<title>Orvel Business Card</title>
<link href="https://fonts.googleapis.com/css2?family=Source+Sans+3:wght@400;600&display=swap" rel="stylesheet">
<style>
  :root {
    --page: #e9e7e4;
    --frost-top: #f7f7f7;
    --frost-bottom: #e6e8ea;
    --band-blue-top: #17a3e4;
    --band-blue-bottom: #1a5ea8;
    --name-ink: #3a4450;
    --band-yellow-top: #fde21a;
    --band-yellow-bottom: #f9b91c;
    --white: #ffffff;
  }
  * { margin: 0; padding: 0; box-sizing: border-box; }
  html, body {
    width: 1200px; height: 900px; overflow: hidden;
    background: var(--page);
    font-family: "Source Sans 3", "Myriad Pro", sans-serif;
  }
  .canvas { position: relative; width: 1200px; height: 900px; }
  .card {
    position: absolute; height: 342px; overflow: hidden;
    background: linear-gradient(180deg, var(--frost-top), var(--frost-bottom));
    box-shadow: 0 4px 14px rgba(0,0,0,0.12);
  }
  .card-front { left: 238px; top: 62px; width: 556px; }
  .card-back { left: 457px; top: 518px; width: 560px; }
  .company-name {
    position: absolute; left: 0; right: 0; top: 88px;
    text-align: center;
    font-size: 56px; font-weight: 600; line-height: 1;
    letter-spacing: 10px; text-transform: uppercase;
    color: var(--name-ink);
  }
  .band-blue {
    position: absolute; left: 0; right: 0; top: 185px; bottom: 0;
    background: linear-gradient(180deg, var(--band-blue-top), var(--band-blue-bottom));
    color: var(--white);
  }
  .contact-list {
    position: absolute; right: 308px; top: 18px; list-style: none;
    font-size: 15px; line-height: 23px; text-align: right;
  }
  .contact-list li { display: flex; justify-content: flex-end; align-items: center; gap: 8px; }
  .contact-list svg { width: 12px; height: 12px; fill: var(--white); flex: none; }
  .holder { position: absolute; left: 290px; top: 18px; font-size: 15px; line-height: 23px; }
  .holder-name { font-size: 21px; font-weight: 600; line-height: 26px; }
  .company-name-faint {
    position: absolute; left: 0; right: 0; top: 80px; text-align: center;
    font-size: 56px; font-weight: 600; line-height: 1;
    letter-spacing: 10px; text-transform: uppercase;
    color: var(--name-ink); opacity: 0.1;
  }
  .band-yellow {
    position: absolute; left: 0; right: 0; top: 187px; bottom: 0;
    background: linear-gradient(135deg, var(--band-yellow-top), var(--band-yellow-bottom) 60%, var(--band-yellow-top));
  }
</style>
</head>
<body>
<main class="canvas">
  <section class="card card-front" aria-label="Business card front">
    <p class="company-name">Orvel</p>
    <div class="band-blue">
      <ul class="contact-list">
        <li>909 555 0142
          <svg viewBox="0 0 12 12"><path d="M2.5 1l2 2-1 1.3c.6 1.4 1.8 2.6 3.2 3.2L8 6.5l2 2-1.2 2C5 10.2 1.8 7 1.5 3.2z"/></svg></li>
        <li>909 555 0187
          <svg viewBox="0 0 12 12"><path d="M3 1h5v3H3zM1.5 4.5h9v6.5h-9zM3.5 6.5h5v1h-5z"/></svg></li>
        <li>626 555 0139
          <svg viewBox="0 0 12 12"><path d="M3 0.5h6v11H3zM4 1.8v7.4h4V1.8z"/></svg></li>
        <li>Daniel@orvelpantry.com
          <svg viewBox="0 0 12 12"><path d="M1 2.5h10v7H1zM1.8 3.2L6 6.4l4.2-3.2z"/></svg></li>
        <li>www.orvelpantry.com
          <svg viewBox="0 0 12 12"><circle cx="6" cy="6" r="5.5"/></svg></li>
      </ul>
      <div class="holder">
        <p class="holder-name">Daniel Hartono</p>
        <p class="holder-title">President</p>
        <p>Orvel Enterprises Corp.</p>
        <p>2480 E Maple Ave.Ontario</p>
        <p>CA 91761</p>
      </div>
    </div>
  </section>

  <section class="card card-back" aria-label="Business card back">
    <p class="company-name-faint" aria-hidden="true">Orvel</p>
    <div class="band-yellow"></div>
  </section>
</main>
</body>
</html>
```